Visitenkarten-Design für Familienunternehmen (Apotheke)
Zielgruppe
Wir sind ein Familienunternehmen und betreiben 4 Apotheken (alle eigene Namen: Lindenhain-Apotheke; Seeblick-Apotheke; Apotheke Am Grauturm und VelaNord-Apotheke)
Wir beginnen, diese alle unter Zobel-Apotheken zusammenzufassen. www.zobel-apotheken-net.de (die VelaNord-Apotheke eröffnet erst am 1.1.18 neu, daher noch nicht online)
Konkret möchten wir für die Mitarbeiter der VelaNord-Apotheke Visitenkarten mit Porträt für Kunden erstellen.
Aktuell sind wir ca. 10 Mitarbeiter in dieser Apotheke. Ggf. möchten wir mittelfristig alle Mitarbeiter aller Apotheken (ca. 50-60) mit Visitenkarten ausstatten.
Aufgabenstellung
Wir haben vor Jahren selbst laienhaft eine Visitenkarte erstellt
Ich habe gegoogelt und andere Beispiele mit Porträt gefunden.
Wir suchen eine Visitenkarte, die sowohl das Logo VelaNord-Apotheke inkl. Adresse, Telefonnummer etc. hat (kann auch optisch verschoben werden - oben Logo - unten Adresse o.ä) , den Namen des Mitarbeitern und Beruf (Apothekerin o.ä.) und 2-3 Schlagwörter/Schlagsätze zu der Qualifikation des Mitarbeiters.
(die VelaNord-Apotheke hat eine Spezialzertifizierung 'Wiegenkreis Apotheke' und darf daher auch das Logo Wiegenkreis Apotheke nutzen. Eventuell gibt es die Möglichkeit dieses auch - nicht konkurrierend - neben dem Hauptlogo VelaNord-Apotheke unterzubringen)
unten gerne 'Zobel-Apotheken' o.ä. als Dachmarke
Mutter-Kind-Expertin (Zertifizierung Wiegenkreis Apotheke)
Fachberaterin für Darmgesundheit
!! Seriös, weniger verspielt. Druckbar für Druckwelle, wir nehmen gerne Tipps zu Papier und Stärke an!
Ziel: Klares Design, wo einfach der Kopf des Mitarbeiters gewechselt werden kann und die Qualifikation, um für alle Mitarbeiter gleiche CI zu erstellen

```html
<!DOCTYPE html>
<html lang="de">
<head>
<meta charset="utf-8">
<title>Visitenkarte VelaNord-Apotheke</title>
<link rel="stylesheet" href="https://fonts.googleapis.com/css2?family=Open+Sans:ital,wght@0,400;0,700;1,400&display=swap">
<style>
  :root {
    --backdrop: #cfbf94;
    --card: #ffffff;
    --ink: #1c1c1c;
    --accent: #d6151c;
    --badge-tint: #f7e1e1;
    --muted: #a8a8a8;
    --text-grey: #555555;
    --portrait-top: #6b4a36;
    --portrait-bottom: #1f2a44;
  }
  * { box-sizing: border-box; margin: 0; padding: 0; }
  html, body {
    width: 1015px; height: 1200px; overflow: hidden;
    background: var(--backdrop);
    font-family: "Open Sans", Arial, sans-serif;
  }
  .sheet {
    width: 1015px; height: 1200px;
    display: flex; flex-direction: column; align-items: center; justify-content: center;
    gap: 70px;
  }
  .card {
    position: relative;
    width: 680px; height: 440px;
    background: var(--card);
    box-shadow: 0 14px 30px rgba(0,0,0,.18);
    overflow: hidden;
  }
  /* Vorderseite */
  .card-front { display: flex; align-items: center; justify-content: center; gap: 16px; }
  .brand-name {
    font-weight: 700; font-size: 50px; letter-spacing: -1px; color: var(--ink);
  }
  .brand-dot {
    width: 26px; height: 26px; border-radius: 50%; background: var(--accent);
  }
  /* Rückseite */
  .card-back {
    background: linear-gradient(200deg, #b9b9b9 0%, #e8e8e8 22%, #ffffff 45%);
  }
  .cert-badge {
    position: absolute; left: 44px; top: 96px;
    width: 150px; height: 64px;
    border-radius: 32px;
    background: var(--badge-tint);
  }
  .contact {
    position: absolute; left: 330px; top: 30px;
    font-size: 11px; line-height: 15px; color: var(--text-grey);
  }
  .contact .web-main { color: var(--accent); }
  .person { position: absolute; left: 44px; bottom: 70px; }
  .person-name { font-weight: 700; font-size: 26px; color: var(--ink); letter-spacing: .5px; }
  .person-branch { font-style: italic; font-size: 18px; color: var(--accent); margin-top: 2px; }
  .person-role { font-size: 16px; color: var(--muted); margin-top: 2px; letter-spacing: .4px; }
  .portrait {
    position: absolute; right: 34px; bottom: 0;
    width: 250px; height: 280px;
    background: linear-gradient(180deg, var(--portrait-top) 0%, #c9a48c 45%, var(--portrait-bottom) 100%);
  }
</style>
</head>
<body>
  <main class="sheet">
    <section class="card card-front" aria-label="Vorderseite">
      <span class="brand-name">VelaNord-Apotheke</span>
      <span class="brand-dot"></span>
    </section>

    <section class="card card-back" aria-label="Rückseite">
      <div class="cert-badge" role="img" aria-label="Platz für das Zertifikatszeichen Wiegenkreis Apotheke"></div>

      <div class="contact">
        <p>Kesselgasse 8 - 93047 Talbruck - Tel.: 0941 / 58 20 140</p>
        <p>Fax: 58 20 141 - velanord@zobel-apotheken-net.de</p>
        <p class="web-main">www.zobel-apotheken-net.de</p>
        <p>www.wiegenkreis-netz.de</p>
      </div>

      <div class="person">
        <p class="person-name">Carla Wendeborn</p>
        <p class="person-branch">Apotheke Am Grauturm</p>
        <p class="person-role">Apothekerin und andere Qualifikation</p>
      </div>

      <div class="portrait" role="img" aria-label="Porträtfoto der Mitarbeiterin"></div>
    </section>
  </main>
</body>
</html>
```